Need Business Card for our Real Estate Business with Sales Executive's Picture

PANTONE 484 C ( RED)

PANTONE 2766 C ( BLUE

Industry/Entity Type

Real Estate

Contact Information for Business Card

Name, Mobile, email, & picture of Person
Agency Phone, address, Web address

Requirements
Must have
• Our Logo Colours, Agent Picture,

```html
<!DOCTYPE html>
<html lang="en">
<head>
<meta charset="utf-8">
<title>Meridian Real Estate – Business Card</title>
<link rel="stylesheet" href="https://fonts.googleapis.com/css2?family=Cinzel:wght@500;600&family=Tinos&display=swap">
<style>
  :root {
    --page: #e8e5e0;
    --card-top: #f4f3f1;
    --card-bottom: #dedad6;
    --navy: #1c2230;
    --maroon: #5b1e22;
    --ink: #1a1d26;
    --photo-light: #c9c3bd;
    --photo-dark: #8d857e;
    --shadow: rgba(0,0,0,0.18);
  }
  html, body {
    margin: 0;
    width: 1200px;
    height: 970px;
    overflow: hidden;
    background: var(--page);
  }
  .business-card {
    position: absolute;
    left: 80px;
    top: 190px;
    width: 1040px;
    height: 592px;
    background: linear-gradient(170deg, var(--card-top) 0%, var(--card-bottom) 100%);
    box-shadow: 0 14px 40px var(--shadow);
    overflow: hidden;
    font-family: "Tinos", "Times New Roman", serif;
    color: var(--ink);
  }
  .roof-shape {
    position: absolute;
    left: 0;
    top: 0;
  }
  .brand-name {
    position: absolute;
    left: 600px;
    top: 280px;
    width: 400px;
    text-align: center;
    font-family: "Cinzel", serif;
    font-weight: 600;
    font-size: 44px;
    letter-spacing: 3px;
    line-height: 1.15;
    color: var(--navy);
  }
  .agent-photo {
    position: absolute;
    left: 55px;
    top: 282px;
    width: 84px;
    height: 84px;
    border-radius: 50%;
    background: linear-gradient(160deg, var(--photo-light) 0%, var(--photo-dark) 100%);
    border: 2px solid var(--maroon);
    box-sizing: border-box;
  }
  .agent-name {
    position: absolute;
    left: 55px;
    top: 380px;
    font-family: "Cinzel", serif;
    font-weight: 500;
    font-size: 32px;
    letter-spacing: 1px;
    color: var(--navy);
    line-height: 1;
  }
  .agent-role {
    position: absolute;
    left: 55px;
    top: 413px;
    font-size: 22px;
    color: var(--maroon);
  }
  .divider-line {
    position: absolute;
    left: 55px;
    top: 457px;
    width: 925px;
    height: 2px;
    background: var(--maroon);
  }
  .contact-column {
    position: absolute;
    top: 481px;
    display: flex;
    flex-direction: column;
    gap: 8px;
    font-size: 24px;
    line-height: 30px;
  }
  .contact-column.phones { left: 55px; }
  .contact-column.online { left: 322px; }
  .contact-column.address { left: 691px; }
  .contact-row {
    display: flex;
    align-items: center;
    gap: 12px;
    white-space: nowrap;
  }
  .contact-icon { width: 30px; height: 30px; flex: none; }
  .column-rule {
    position: absolute;
    top: 488px;
    width: 3px;
    height: 60px;
    background: var(--navy);
  }
  .column-rule.first { left: 292px; }
  .column-rule.second { left: 663px; }
</style>
</head>
<body>
<div class="business-card">
  <svg class="roof-shape" width="1040" height="300" viewBox="0 0 1040 300" aria-hidden="true">
    <polygon points="0,0 1040,0 1040,192 731,57 0,238" fill="var(--navy)"/>
    <polygon points="731,60 0,244 0,282" fill="var(--maroon)"/>
    <polygon points="731,60 1040,198 1040,262" fill="var(--maroon)"/>
  </svg>

  <div class="brand-name">MERIDIAN<br>REAL ESTATE</div>

  <div class="agent-photo" role="img" aria-label="Portrait photo of the sales executive"></div>
  <div class="agent-name">Daniel Reyes</div>
  <div class="agent-role">Owner</div>

  <div class="divider-line"></div>

  <div class="contact-column phones">
    <div class="contact-row">
      <svg class="contact-icon" viewBox="0 0 30 30" aria-hidden="true"><circle cx="15" cy="15" r="13" fill="none" stroke="var(--maroon)" stroke-width="2"/><rect x="10" y="7" width="10" height="16" rx="2" fill="none" stroke="var(--maroon)" stroke-width="2"/></svg>
      <span>(555) 218-4630</span>
    </div>
    <div class="contact-row">
      <svg class="contact-icon" viewBox="0 0 30 30" aria-hidden="true"><circle cx="15" cy="15" r="13" fill="none" stroke="var(--maroon)" stroke-width="2"/><rect x="10" y="7" width="10" height="16" rx="2" fill="none" stroke="var(--maroon)" stroke-width="2"/></svg>
      <span>(555) 218-4630</span>
    </div>
  </div>

  <div class="column-rule first"></div>

  <div class="contact-column online">
    <div class="contact-row">
      <svg class="contact-icon" viewBox="0 0 30 30" aria-hidden="true"><circle cx="15" cy="15" r="13" fill="none" stroke="var(--maroon)" stroke-width="2"/><rect x="8" y="10" width="14" height="10" fill="var(--maroon)"/><polyline points="8,10 15,16 22,10" fill="none" stroke="#f0eeeb" stroke-width="1.5"/></svg>
      <span>hello@meridianhomes.com</span>
    </div>
    <div class="contact-row">
      <svg class="contact-icon" viewBox="0 0 30 30" aria-hidden="true"><circle cx="15" cy="15" r="13" fill="none" stroke="var(--maroon)" stroke-width="2"/><circle cx="15" cy="15" r="8" fill="none" stroke="var(--maroon)" stroke-width="1.5"/><ellipse cx="15" cy="15" rx="3.5" ry="8" fill="none" stroke="var(--maroon)" stroke-width="1.2"/><line x1="7" y1="15" x2="23" y2="15" stroke="var(--maroon)" stroke-width="1.2"/></svg>
      <span>www.meridianhomes.com</span>
    </div>
  </div>

  <div class="column-rule second"></div>

  <div class="contact-column address">
    <div class="contact-row">PO BOX 480 Harbour Road</div>
    <div class="contact-row">5th street Geelong</div>
  </div>
</div>
</body>
</html>
```